Business card for Crestline Bathrooms

Please design a business card for our bathroom renovation business. You can use my existing logo, but if you have an idea to modernize it, I would like to see it. Please see attached files first. I would like to use the blue and the orange theme. I like the concept of using the shower head in the logo. Please find following a design (or two) that I have been trying to create with my limited resources. That design was for a sign, but I was going to adopt it and use it as a business card as well. I like the concept of the water splash but I don’t think it “flows” nicely together with the logo. Another thought is that maybe creating the logo out of water splash could work and have a dramatic effect (like the water text and the butterfly picture attached with similar background instead of white). If the above doesn’t work I would like to see a modern simplified design. One of the attached files named as the unwanted business card has all the details that I want included in the business card. Please note that it is two sided.
Updates

I am very thankful for the designs that I have received, but they are very similar and only a couple of attempts to do something with the water splash as per my original brief. Modernizing the logo and having it made out of out of water splash with the orange as color accent could work and have a dramatic effect (like the water text and the butterfly picture attached with similar background instead of white). Please do not use the butterfly itself! This is just an example that images can be created out of water splash.

Contact Information for Business Card

all the details are on the unwonted business card file included

Colors
3176b5

Requirements
Nice to have
• Copied from the brief:
• ... maybe creating the logo out of water splash could work and have a dramatic effect (like the water text and the butterfly picture attached with similar background instead of white). Please do not use the butterfly itself!
Should not have
• I am getting designs with a butterfly. The butterfly picture was an example of creating something from a water splash. The butterfly itself has no association with anything other than the concept of creating a logo out of water splash. Sorry, I thought I was clear in the brief.

```html
<!DOCTYPE html>
<html lang="en">
<head>
<meta charset="utf-8">
<title>Crestline Bathrooms – Business Card</title>
<link href="https://fonts.googleapis.com/css2?family=Patrick+Hand&family=Roboto:wght@400;500&family=Roboto+Condensed:wght@400&display=swap" rel="stylesheet">
<style>
  :root {
    --page-bg: #e6e6e6;
    --card-navy: #1a2f50;
    --splash-deep: #27507e;
    --splash-light: #6d93b8;
    --splash-foam: #c9d8e6;
    --accent-coral: #e8735f;
    --text-white: #ffffff;
  }
  * { margin: 0; padding: 0; box-sizing: border-box; }
  html, body { width: 1200px; height: 960px; overflow: hidden; }
  body { background: var(--page-bg); position: relative; font-family: "Roboto", sans-serif; }

  .card {
    position: absolute;
    width: 600px;
    height: 343px;
    background: var(--card-navy);
    overflow: hidden;
  }
  .card--front { left: 302px; top: 124px; }
  .card--back  { left: 299px; top: 493px; }

  .splash {
    position: absolute;
    left: 0; top: 0;
    width: 290px; height: 100%;
    background:
      radial-gradient(ellipse 150px 90px at 150px 300px, var(--splash-foam) 0%, rgba(201,216,230,0.35) 45%, rgba(26,47,80,0) 100%),
      radial-gradient(ellipse 60px 160px at 30px 230px, rgba(201,216,230,0.45) 0%, rgba(26,47,80,0) 100%),
      linear-gradient(90deg, var(--splash-deep) 0%, #2a4f7a 45%, var(--card-navy) 100%);
  }

  .contact { position: absolute; left: 276px; top: 92px; }
  .contact__name {
    font-family: "Patrick Hand", cursive;
    font-size: 29px;
    letter-spacing: 1px;
    color: var(--accent-coral);
    font-weight: 400;
    line-height: 1;
    margin-bottom: 17px;
  }
  .contact__list { list-style: none; }
  .contact__item {
    display: flex; align-items: center;
    height: 20px;
    font-size: 14.5px;
    color: var(--text-white);
  }
  .contact__icon { width: 13px; height: 13px; margin-right: 11px; fill: var(--accent-coral); flex: none; }

  .brand { position: absolute; left: 266px; top: 52px; display: flex; align-items: center; }
  .brand__dot { width: 16px; height: 16px; border-radius: 50%; background: var(--accent-coral); margin-right: 10px; }
  .brand__name {
    font-family: "Roboto", sans-serif;
    font-weight: 500;
    font-size: 26px;
    color: var(--text-white);
    line-height: 1.15;
  }

  .services {
    position: absolute; left: 266px; top: 174px;
    list-style: none;
    font-family: "Roboto Condensed", sans-serif;
    font-size: 14.5px;
    color: var(--text-white);
  }
  .services__item { height: 20px; display: flex; align-items: center; }
  .services__item::before {
    content: ""; width: 5px; height: 5px; border-radius: 50%;
    background: var(--accent-coral); margin-right: 8px;
  }

  .memberships { position: absolute; left: 266px; top: 266px; display: flex; align-items: center; }
  .memberships__badge { width: 26px; height: 28px; border-radius: 4px; background: var(--text-white); }
  .memberships__rule { width: 1px; height: 26px; background: var(--text-white); margin: 0 10px; }
  .memberships__badge--wide { width: 120px; height: 22px; border-radius: 2px; }
</style>
</head>
<body>
  <section class="card card--front" aria-label="Card front">
    <div class="splash" role="img" aria-label="Photograph of water droplets and a splash"></div>
    <div class="contact">
      <h1 class="contact__name">Daniel Hartwell</h1>
      <ul class="contact__list">
        <li class="contact__item"><svg class="contact__icon" viewBox="0 0 16 16"><path d="M4 0h8a1 1 0 0 1 1 1v14a1 1 0 0 1-1 1H4a1 1 0 0 1-1-1V1a1 1 0 0 1 1-1zm1 2v10h6V2zm3 11a1 1 0 1 0 0 2 1 1 0 0 0 0-2z"/></svg>6120 4481</li>
        <li class="contact__item"><svg class="contact__icon" viewBox="0 0 16 16"><path d="M3.6 0.5l2.2 3.3-1.5 1.6c.9 2.2 2.4 3.8 4.5 4.9l1.6-1.5 3.3 2.1-.8 3.4C7 14.2 1.5 8.6 1.1 1.4z"/></svg>0412 583 207</li>
        <li class="contact__item"><svg class="contact__icon" viewBox="0 0 16 16"><path d="M0 3h16v10H0zm1.5 1.2v.4L8 9l6.5-4.4v-.4z"/></svg>daniel@crestlinebathrooms.com.au</li>
        <li class="contact__item"><svg class="contact__icon" viewBox="0 0 16 16"><path d="M8 0a8 8 0 1 0 0 16A8 8 0 0 0 8 0zm-1 2.2c-.5 1-1.8 1.3-2 2.5.8.6 1.9.3 2.3 1.3-.5 1.1-2 1.2-1.7 2.6.7 1 .4 2.3.9 3.5C4 11.6 2 9.9 2 8a6 6 0 0 1 5-5.8zm4 1.3c1.5 1 2.5 2.7 2.5 4.5 0 1.2-.4 2.3-1 3.2-.8-.6-.6-1.9-1.6-2.3-1.1 0-1.6-1-1.3-2 .6-.8 1.5-1.2 1.4-2.4z"/></svg>www.crestlinebathrooms.com.au</li>
        <li class="contact__item"><svg class="contact__icon" viewBox="0 0 16 16"><path d="M8 0a5.5 5.5 0 0 0-5.5 5.5C2.5 9.6 8 16 8 16s5.5-6.4 5.5-10.5A5.5 5.5 0 0 0 8 0zm0 3a2.5 2.5 0 1 1 0 5 2.5 2.5 0 0 1 0-5z"/></svg>PO Box 41, Larkfield 2620</li>
      </ul>
    </div>
  </section>

  <section class="card card--back" aria-label="Card back">
    <div class="splash" role="img" aria-label="Photograph of water droplets and a splash"></div>
    <div class="brand">
      <span class="brand__dot"></span>
      <span class="brand__name">Crestline Bathrooms</span>
    </div>
    <ul class="services">
      <li class="services__item">Complete Bathroom Renovations &amp; Remodelling</li>
      <li class="services__item">Highly Skilled &amp; Qualified Tradespeople</li>
      <li class="services__item">Professional Service From Concept To Completion</li>
      <li class="services__item">All Work Guaranteed</li>
    </ul>
    <div class="memberships" aria-label="Industry memberships">
      <span class="memberships__badge"></span>
      <span class="memberships__rule"></span>
      <span class="memberships__badge memberships__badge--wide"></span>
    </div>
  </section>
</body>
</html>
```